Looking for a modern, Professional business card design

We have a simple business card, but are looking for a more modern, professional look. A sample of the basic card is attached as well as the logo. We would also like to add that we offer:
Struggling with your finances?
- Learn to become debt free
- Discover the power of cash
- Control your money instead of it controlling you
Let us help you achieve a new level of financial freedom!
Also, we would like to have a "SPECIAL OFFER!: FREE 30 minute consultation"
Financial Planning

```html
<!DOCTYPE html>
<html lang="en">
<head>
<meta charset="utf-8">
<title>Openroad Financial Coaching – Business Card</title>
<link href="https://fonts.googleapis.com/css2?family=Josefin+Sans:wght@400;600;700&family=Russo+One&display=swap" rel="stylesheet">
<style>
  :root {
    --stage: #2b2b2d;
    --card: #050505;
    --green-light: #7ac943;
    --green-dark: #2f8f3c;
    --white: #ffffff;
  }
  * { box-sizing: border-box; margin: 0; padding: 0; }
  html, body { width: 1200px; height: 900px; overflow: hidden; }
  body {
    background: var(--stage);
    font-family: "Josefin Sans", sans-serif;
    color: var(--white);
    position: relative;
  }
  .card {
    position: absolute;
    width: 620px;
    height: 354px;
    background: var(--card);
    border-radius: 18px;
    overflow: hidden;
    box-shadow: 0 18px 40px rgba(0,0,0,.5);
  }
  .card--back { left: 60px; top: 60px; }
  .card--front { left: 520px; top: 486px; }

  /* bottom bands */
  .band-dark, .band-light { position: absolute; bottom: 0; }
  .band-dark {
    left: 0; width: 58%; height: 22px;
    background: var(--green-dark);
    clip-path: polygon(0 35%, 100% 35%, 100% 100%, 0 100%);
  }
  .band-light {
    right: 0; width: 42%; height: 22px;
    background: var(--green-light);
  }
  .band-edge {
    position: absolute; left: 0; right: 0; bottom: 0; height: 8px;
    background: var(--green-light);
  }
  .rule {
    position: absolute; height: 2px; background: var(--green-dark);
  }
  .rule--title { left: 300px; right: 34px; top: 102px; }
  .rule--contact { left: 0; right: 0; top: 196px; }

  /* brand */
  .brand-dot {
    width: 18px; height: 18px; border-radius: 50%;
    background: var(--green-light); flex: none;
  }
  .brand-name {
    font-weight: 700; font-size: 26px; color: var(--green-light);
    letter-spacing: .5px; text-transform: uppercase;
  }

  /* back card */
  .brand-mark {
    position: absolute; left: 0; right: 0; top: 50px;
    display: flex; align-items: center; justify-content: center; gap: 12px;
  }
  .pitch {
    position: absolute; left: 0; right: 0; top: 150px;
    text-align: center; font-size: 17px; line-height: 26px;
  }
  .pitch .accent { color: var(--green-light); }
  .pitch .caps { text-transform: uppercase; font-weight: 600; }

  /* front card */
  .front-brand {
    position: absolute; left: 38px; top: 104px;
    display: flex; align-items: center; gap: 12px;
  }
  .front-brand .brand-name {
    font-size: 22px; line-height: 26px; width: 240px;
  }
  .person {
    position: absolute; right: 34px; top: 36px; text-align: right;
  }
  .person-name {
    font-family: "Russo One", sans-serif; font-size: 26px; line-height: 32px;
    color: var(--green-light); text-transform: uppercase; letter-spacing: 1px;
  }
  .person-title {
    font-family: "Russo One", sans-serif; font-size: 13px;
    text-transform: uppercase; letter-spacing: 1px; margin-top: 4px;
  }
  .offer {
    position: absolute; right: 34px; top: 120px; text-align: right;
    font-size: 18px; line-height: 24px;
  }
  .offer-label {
    font-family: "Russo One", sans-serif; color: var(--green-light);
    text-transform: uppercase; font-size: 15px;
  }
  .offer-free { font-family: "Russo One", sans-serif; font-size: 15px; }
  .offer-line { color: var(--green-light); }
  .contact {
    position: absolute; left: 38px; top: 210px;
    list-style: none; font-size: 17px;
  }
  .contact li { display: flex; align-items: center; gap: 14px; height: 30px; }
  .contact svg { width: 16px; height: 16px; flex: none; }
  .contact .accent { color: var(--green-light); }
</style>
</head>
<body>

<section class="card card--back" aria-label="Card back">
  <div class="brand-mark">
    <span class="brand-dot"></span>
    <span class="brand-name">Openroad Financial Coaching</span>
  </div>
  <div class="pitch">
    <p class="caps"><span class="accent">Struggling</span> with your <span class="accent">finances?</span></p>
    <p>Learn to become debt free</p>
    <p>Discover the power of cash</p>
    <p>Control your money instead of it controlling you</p>
    <p>Let us help you achieve a new level of financial <span class="accent caps">freedom!</span></p>
  </div>
  <div class="band-dark"></div>
  <div class="band-light"></div>
  <div class="band-edge"></div>
</section>

<section class="card card--front" aria-label="Card front">
  <div class="front-brand">
    <span class="brand-dot"></span>
    <span class="brand-name">Openroad Financial Coaching</span>
  </div>

  <div class="person">
    <p class="person-name">Daniel R. Whitfield</p>
    <p class="person-title">Personal Financial Coach</p>
  </div>
  <div class="rule rule--title"></div>

  <div class="offer">
    <p><span class="offer-label">Special Offer!</span> <span class="offer-free">FREE</span> 30</p>
    <p class="offer-line">minute consultation</p>
  </div>

  <div class="rule rule--contact"></div>

  <ul class="contact">
    <li>
      <svg viewBox="0 0 16 16" aria-hidden="true"><rect x="4" y="1" width="8" height="14" rx="1.5" fill="none" stroke="#7ac943" stroke-width="1.6"/><circle cx="8" cy="12.5" r=".9" fill="#7ac943"/></svg>
      <span>(205) 555-0148</span>
    </li>
    <li>
      <svg viewBox="0 0 16 16" aria-hidden="true"><rect x="1" y="3.5" width="14" height="9" rx="1" fill="none" stroke="#7ac943" stroke-width="1.6"/><path d="M1.5 4l6.5 5 6.5-5" fill="none" stroke="#7ac943" stroke-width="1.6"/></svg>
      <span>daniel@openroadmoneycoach.com</span>
    </li>
    <li>
      <svg viewBox="0 0 16 16" aria-hidden="true"><circle cx="8" cy="8" r="6.5" fill="none" stroke="#7ac943" stroke-width="1.5"/><ellipse cx="8" cy="8" rx="3" ry="6.5" fill="none" stroke="#7ac943" stroke-width="1.2"/><path d="M1.5 8h13M2.5 5h11M2.5 11h11" stroke="#7ac943" stroke-width="1.1"/></svg>
      <span>www.<span class="accent">openroadmoneycoach</span>.com</span>
    </li>
  </ul>

  <div class="band-dark"></div>
  <div class="band-light"></div>
  <div class="band-edge"></div>
</section>

</body>
</html>
```